Brand Identity Stationary Package

Hello I'm looking for a full branding package for my Property Management Company. I have a logo but looking to have the following
Business Card
Email signature
Facebook cover photo
Letterhead (word.doc)
#10 Envelope
Pocket Folder - link to 9x12 pocket folder design specs https://www.printorbit-example.ca/marketing-materials/presentation-folders
would like everything to match and be brand identifiable. The company looks after residential properties/apartments and some commercial properties. Attached is a zip of the files.
For Business Card
Name: Gareth Lindqvist
Position: Operations Manager
Number: 1 (555) 384-2917
Email: Gareth@harborkey-example.ca
Website: Harborkey-example.ca
Property Management

```html
<!DOCTYPE html>
<html lang="en">
<head>
<meta charset="utf-8">
<title>Harborkey Business Card</title>
<link href="https://fonts.googleapis.com/css2?family=Montserrat:wght@700&family=Roboto:wght@300;400;700&display=swap" rel="stylesheet">
<style>
  :root {
    --backdrop: #d6d6d6;
    --card-white: #ffffff;
    --brand-black: #161616;
    --brand-green: #7ba726;
    --text-light: #ffffff;
  }
  html, body {
    margin: 0;
    padding: 0;
    width: 1200px;
    height: 800px;
    overflow: hidden;
    background: var(--backdrop);
  }
  .stage {
    position: relative;
    width: 1200px;
    height: 800px;
  }
  .card {
    position: absolute;
    top: 252px;
    width: 520px;
    height: 297px;
    border-radius: 18px;
    overflow: hidden;
    box-shadow: 0 10px 24px rgba(0, 0, 0, 0.18);
  }
  .card--front { left: 60px; background: var(--card-white); }
  .card--back { left: 620px; background: var(--brand-black); }

  .card__shapes {
    position: absolute;
    inset: 0;
  }
  .wordmark {
    position: absolute;
    font-family: "Montserrat", sans-serif;
    font-weight: 700;
    letter-spacing: 1px;
    display: flex;
    align-items: center;
    gap: 8px;
    white-space: nowrap;
  }
  .wordmark__dot {
    width: 8px;
    height: 8px;
    background: var(--brand-green);
  }
  .card--front .wordmark {
    left: 28px;
    top: 136px;
    font-size: 20px;
    color: var(--brand-black);
  }
  .card--back .wordmark {
    left: 0;
    right: 0;
    top: 128px;
    justify-content: center;
    font-size: 40px;
    gap: 10px;
    color: var(--text-light);
  }
  .card--back .wordmark__dot {
    width: 10px;
    height: 10px;
  }

  .contact {
    position: absolute;
    right: 30px;
    top: 90px;
    text-align: right;
    color: var(--text-light);
    font-family: "Roboto", sans-serif;
    white-space: nowrap;
  }
  .contact__name {
    margin: 0;
    font-size: 23px;
    font-weight: 700;
    line-height: 1.1;
  }
  .contact__role {
    margin: 2px 0 14px;
    font-size: 13px;
    font-weight: 300;
  }
  .contact__list {
    list-style: none;
    margin: 0;
    padding: 0;
    font-size: 12.5px;
    font-weight: 400;
    line-height: 1.55;
  }
  .contact__item {
    display: flex;
    justify-content: flex-end;
    align-items: center;
    gap: 7px;
  }
  .contact__icon {
    width: 11px;
    height: 11px;
    flex: none;
  }
</style>
</head>
<body>
<main class="stage">

  <section class="card card--front" aria-label="Business card front">
    <svg class="card__shapes" viewBox="0 0 520 297" width="520" height="297" aria-hidden="true">
      <rect x="290" y="0" width="16" height="18" fill="var(--brand-black)"/>
      <polygon points="155,297 285,12 520,12 520,297" fill="var(--brand-black)"/>
      <polygon points="195,297 305,42 520,42 520,297" fill="var(--brand-green)"/>
    </svg>

    <div class="wordmark">
      <span>HARBORKEY</span>
      <span class="wordmark__dot"></span>
    </div>

    <div class="contact">
      <h1 class="contact__name">Gareth Lindqvist</h1>
      <p class="contact__role">Operations Manager</p>
      <ul class="contact__list">
        <li class="contact__item">
          <span>1 (555) 384-2917</span>
          <svg class="contact__icon" viewBox="0 0 12 12" aria-hidden="true">
            <path d="M2.5 1 L4.5 1 L5.3 3.6 L4 4.6 C4.7 6 6 7.3 7.4 8 L8.4 6.7 L11 7.5 L11 9.5 C11 10.3 10.3 11 9.5 11 C5 11 1 7 1 2.5 C1 1.7 1.7 1 2.5 1 Z" fill="var(--text-light)"/>
          </svg>
        </li>
        <li class="contact__item">
          <span>Gareth@harborkey-example.ca</span>
          <svg class="contact__icon" viewBox="0 0 12 12" aria-hidden="true">
            <rect x="0.5" y="2" width="11" height="8" fill="var(--text-light)"/>
            <path d="M0.5 2 L6 6.5 L11.5 2" fill="none" stroke="var(--brand-green)" stroke-width="1.1"/>
          </svg>
        </li>
        <li class="contact__item">
          <span>www.Harborkey-example.ca</span>
          <svg class="contact__icon" viewBox="0 0 12 12" aria-hidden="true">
            <circle cx="6" cy="6" r="5.2" fill="none" stroke="var(--text-light)" stroke-width="1.2"/>
            <ellipse cx="6" cy="6" rx="2.2" ry="5.2" fill="none" stroke="var(--text-light)" stroke-width="1"/>
            <line x1="0.8" y1="6" x2="11.2" y2="6" stroke="var(--text-light)" stroke-width="1"/>
          </svg>
        </li>
      </ul>
    </div>
  </section>

  <section class="card card--back" aria-label="Business card back">
    <div class="wordmark">
      <span>HARBORKEY</span>
      <span class="wordmark__dot"></span>
    </div>
  </section>

</main>
</body>
</html>
```